Quote Cards With KB May 2025 for Instagram

I would like to put these quotes over one of the pictures attached; Instagram (new size: 4:5 (1080 x 1350 pixels) One Quote per picture, and I want the quote to be bold or easy to read as well. I provided a few reference graphics that I really like as examples below. In very small letters at the bottom add @KBHarlowOnline

All of the pictures are attached; you can pick any photo and add one quote to it; but no stock photography

```html
<!DOCTYPE html>
<html lang="en">
<head>
<meta charset="utf-8">
<title>KB Quote Cards – May 2025</title>
<link href="https://fonts.googleapis.com/css2?family=Antonio:wght@400;500;600;700&display=swap" rel="stylesheet">
<style>
  :root{
    --page:#ffffff;
    --ink-dark:#1c1416;
    --ink-light:#ffffff;
    --blush-box:rgba(240,216,226,0.93);
    --mauve-box:rgba(128,62,88,0.84);
    --panel-top:#181014;
    --panel-mid:#261520;
    --panel-bottom:#4e2438;
    --room-light:#eceaee;
    --room-mid:#cfcad1;
    --kitchen-dark:#3a1418;
    --kitchen-mid:#6e2a32;
    --glow-pink:#e48ac0;
    --glow-violet:#7a4c90;
    --glow-deep:#2a1a2e;
    --subject-top:rgba(24,16,22,0.55);
    --subject-bottom:rgba(24,16,22,0.85);
    --subject-edge:rgba(255,255,255,0.35);
  }
  *{margin:0;padding:0;box-sizing:border-box}
  html,body{width:960px;height:1200px;overflow:hidden;background:var(--page)}
  body{font-family:"Antonio",sans-serif;text-transform:uppercase}
  .board{
    width:960px;height:1200px;
    display:grid;
    grid-template-columns:314px 314px 314px;
    grid-template-rows:394px 394px 394px;
    column-gap:9px;row-gap:9px;
  }
  .card{position:relative;overflow:hidden}
  .photo{position:absolute;inset:0}
  .photo--room{background:linear-gradient(180deg,var(--room-light) 0%,var(--room-mid) 60%,#a9a2ac 100%)}
  .photo--kitchen{background:linear-gradient(180deg,var(--kitchen-mid) 0%,var(--kitchen-dark) 55%,#2a1c1a 100%)}
  .photo--glow{background:linear-gradient(180deg,var(--glow-pink) 0%,var(--glow-violet) 45%,var(--glow-deep) 100%)}
  .photo--dusk{background:linear-gradient(180deg,#dba4ca 0%,#a878a8 40%,#4d3b52 75%,#243024 100%)}

  .subject{
    position:absolute;
    background:linear-gradient(180deg,var(--subject-top),var(--subject-bottom));
    border:1px solid var(--subject-edge);
    border-radius:70px 70px 10px 10px;
  }

  .quote-box{position:absolute}
  .quote-box--blush{left:9px;top:9px;width:295px;height:156px;background:var(--blush-box);color:var(--ink-dark)}
  .quote-box--mauve{left:19px;top:216px;width:284px;height:152px;background:var(--mauve-box);color:var(--ink-light)}

  .panel{
    position:absolute;top:0;bottom:0;color:var(--ink-light);
    background:linear-gradient(180deg,var(--panel-top) 0%,var(--panel-mid) 55%,var(--panel-bottom) 100%);
  }
  .panel--left{left:9px;width:196px}
  .panel--left-edge{left:0;width:188px}
  .panel--right{left:129px;width:186px}

  .t{position:absolute;left:0;right:0;line-height:1;white-space:nowrap;font-weight:600;text-align:center;letter-spacing:0.2px}
  .t--left{left:14px;right:auto;text-align:left}
  .t--right{left:auto;right:10px;text-align:right}
  .t--light{font-weight:500}

  .handle{position:absolute;left:0;right:0;text-align:center;font-size:8px;font-weight:500;line-height:1;letter-spacing:0.2px}
  .handle--left{left:14px;right:auto;text-align:left}
  .handle--onphoto{color:var(--ink-light)}
</style>
</head>
<body>
<main class="board">

  <!-- Row 1 -->
  <section class="card">
    <div class="photo photo--room" role="img" aria-label="Photo of KB in a black outfit, hand on hip, in a bright room">
      <div class="subject" style="left:95px;top:172px;width:155px;height:230px"></div>
    </div>
    <div class="quote-box quote-box--blush">
      <span class="t t--light" style="top:16px;font-size:18px">Bloating. Muffin top. Puffy waistline.</span>
      <span class="t" style="top:42px;font-size:26px">Your body's screaming for a</span>
      <span class="t" style="top:68px;font-size:26px">different kind of fix.</span>
      <span class="t" style="top:98px;font-size:36px">Here it is.</span>
      <span class="handle" style="top:139px">@KBHarlowOnline</span>
    </div>
  </section>

  <section class="card">
    <div class="photo photo--kitchen" role="img" aria-label="Photo of KB in a sheer striped top pointing down, in a dark red kitchen">
      <div class="subject" style="left:42px;top:18px;width:236px;height:210px"></div>
    </div>
    <div class="quote-box quote-box--mauve">
      <span class="t t--light" style="top:14px;font-size:20px">Tired. Moody. Stubborn belly fat.</span>
      <span class="t" style="top:44px;font-size:28px;letter-spacing:0.8px">Your hormones are</span>
      <span class="t" style="top:74px;font-size:28px;letter-spacing:0.8px">screaming for help!</span>
      <span class="t" style="top:110px;font-size:37px;letter-spacing:2px">Let's fix that.</span>
    </div>
    <span class="handle handle--onphoto" style="top:375px">@KBHarlowOnline</span>
  </section>

  <section class="card">
    <div class="photo photo--room" role="img" aria-label="Photo of KB in a white cropped sweater, arms raised, in a bright room">
      <div class="subject" style="left:62px;top:168px;width:196px;height:234px"></div>
    </div>
    <div class="quote-box quote-box--blush">
      <span class="t t--light" style="top:16px;font-size:22px">The stubborn belly fat after 40?</span>
      <span class="t" style="top:44px;font-size:27px">It's not about calories;</span>
      <span class="t" style="top:70px;font-size:27px">it's about your hormones.</span>
      <span class="t" style="top:104px;font-size:31px">Here is the fix!</span>
      <span class="handle" style="top:139px">@KBHarlowOnline</span>
    </div>
  </section>

  <!-- Row 2 -->
  <section class="card">
    <div class="photo photo--glow" role="img" aria-label="Photo of KB smiling in a pink sparkly outfit">
      <div class="subject" style="left:214px;top:42px;width:92px;height:360px"></div>
    </div>
    <div class="panel panel--left">
      <span class="t t--left t--light" style="top:34px;font-size:25px">This 90-day plan</span>
      <span class="t t--left t--light" style="top:64px;font-size:25px">helped women</span>
      <span class="t t--left t--light" style="top:94px;font-size:25px">over 40 slim down</span>
      <span class="t t--left t--light" style="top:145px;font-size:25px">Get a tiny waist</span>
      <span class="t t--left t--light" style="top:177px;font-size:25px">and feel sexy</span>
      <span class="t t--left t--light" style="top:209px;font-size:25px">again.</span>
      <span class="t t--left" style="top:292px;font-size:40px;left:2px">You're next.</span>
      <span class="handle handle--left" style="top:364px">@KBHarlowOnline</span>
    </div>
  </section>

  <section class="card">
    <div class="photo photo--glow" role="img" aria-label="Photo of KB standing in a bronze top and black jeans against a city night view">
      <div class="subject" style="left:18px;top:36px;width:104px;height:352px"></div>
    </div>
    <div class="panel panel--right">
      <span class="t t--light" style="top:34px;font-size:25px">Your belly</span>
      <span class="t t--light" style="top:65px;font-size:25px">isn't fat.</span>
      <span class="t t--light" style="top:96px;font-size:25px">It's hormonal.</span>
      <span class="t t--light" style="top:142px;font-size:25px">And here's how</span>
      <span class="t t--light" style="top:172px;font-size:25px">to fix it.</span>
      <span class="t t--light" style="top:218px;font-size:25px">Comment</span>
      <span class="t t--light" style="top:250px;font-size:25px">hormones</span>
      <span class="t t--light" style="top:281px;font-size:25px">if nothin</span>
      <span class="t t--light" style="top:312px;font-size:25px">is working.</span>
      <span class="handle" style="top:364px">@KBHarlowOnline</span>
    </div>
  </section>

  <section class="card">
    <div class="photo photo--glow" role="img" aria-label="Photo of KB in a long pink dress">
      <div class="subject" style="left:200px;top:28px;width:108px;height:374px"></div>
    </div>
    <div class="panel panel--left-edge">
      <span class="t t--left t--light" style="top:35px;font-size:26px;left:23px">That stubborn</span>
      <span class="t t--left t--light" style="top:67px;font-size:26px;left:23px">weight?</span>
      <span class="t t--left t--light" style="top:100px;font-size:19px;left:23px">It's not your fault.</span>
      <span class="t t--left t--light" style="top:142px;font-size:25px;left:23px">Your hormones</span>
      <span class="t t--left t--light" style="top:172px;font-size:25px;left:23px">are to blame</span>
      <span class="t t--left t--light" style="top:201px;font-size:25px;left:23px">and you're</span>
      <span class="t t--left t--light" style="top:231px;font-size:25px;left:23px">not alone</span>
      <span class="t t--left" style="top:280px;font-size:34px;left:23px">But there is</span>
      <span class="t t--left" style="top:319px;font-size:34px;left:23px">a fix.</span>
      <span class="handle handle--left" style="top:364px;left:23px">@KBHarlowOnline</span>
    </div>
  </section>

  <!-- Row 3 -->
  <section class="card">
    <div class="photo photo--glow" role="img" aria-label="Photo of KB in a sheer black outfit in front of a city skyline window">
      <div class="subject" style="left:22px;top:28px;width:104px;height:374px"></div>
    </div>
    <div class="panel panel--right">
      <span class="t t--light" style="top:38px;font-size:25px">What worked</span>
      <span class="t t--light" style="top:68px;font-size:25px">in your 30s</span>
      <span class="t t--light" style="top:98px;font-size:25px">won't work now.</span>
      <span class="t t--light" style="top:148px;font-size:25px">Here's what</span>
      <span class="t t--light" style="top:182px;font-size:25px">actually does.</span>
      <span class="t t--light" style="top:240px;font-size:25px">Drop 30 pounds</span>
      <span class="t t--light" style="top:273px;font-size:25px">in 3 months.</span>
      <span class="handle" style="top:365px">@KBHarlowOnline</span>
    </div>
  </section>

  <section class="card">
    <div class="photo photo--dusk" role="img" aria-label="Photo of KB in a black outfit posing outdoors at dusk">
      <div class="subject" style="left:12px;top:34px;width:118px;height:368px"></div>
    </div>
    <div class="panel panel--right" style="width:185px">
      <span class="t" style="top:36px;font-size:31px">Flat tummy</span>
      <span class="t" style="top:68px;font-size:31px">in your 40s?</span>
      <span class="t" style="top:116px;font-size:42px">It's still</span>
      <span class="t" style="top:159px;font-size:42px">possible!</span>
      <span class="t t--right t--light" style="top:236px;font-size:19px">Comment</span>
      <span class="t t--right t--light" style="top:260px;font-size:19px">bye belly to get</span>
      <span class="t t--right t--light" style="top:283px;font-size:19px">the 10 secrets</span>
      <span class="t t--right t--light" style="top:307px;font-size:19px">to a flatter tummy</span>
      <span class="handle" style="top:363px">@KBHarlowOnline</span>
    </div>
  </section>

  <section class="card">
    <div class="photo photo--dusk" role="img" aria-label="Photo of KB in a sheer striped top with arms raised outdoors">
      <div class="subject" style="left:6px;top:48px;width:124px;height:354px"></div>
    </div>
    <div class="panel panel--right" style="width:185px">
      <span class="t t--light" style="top:38px;font-size:25px">This is the secret</span>
      <span class="t t--light" style="top:67px;font-size:25px">women over 40</span>
      <span class="t t--light" style="top:96px;font-size:25px">are using</span>
      <span class="t t--light" style="top:125px;font-size:25px">to get snatched</span>
      <span class="t t--light" style="top:187px;font-size:25px">without starving</span>
      <span class="t t--light" style="top:236px;font-size:26px">Comment skinny</span>
      <span class="t t--light" style="top:268px;font-size:26px">to get</span>
      <span class="t t--light" style="top:300px;font-size:26px">the exact plan.</span>
      <span class="handle" style="top:364px">@KBHarlowOnline</span>
    </div>
  </section>

</main>
</body>
</html>
```